International pain relief company needs flyer designed

We are based in South Australia, and are about to launch a brand new hand held portable fully chargeable pain relief device. This device gives the user proven instant relief often from the first time of use anywhere. We intend to offer, a try before you buy at home /office demonstration, a full 30 day money back guarantee and a full 3 year warranty. We also plan to give the first 7 people who book a demonstration a FREE $20 Norvane fuel card.
We are open minded regarding the overall design and colours used, however we are particularly keen on seeing pictures/cartoons of people suffering from the 3 main groups of pain, head ache, back ache and joint pain, perhaps also happy faces once they have been cured/relieved by our equipment. This product we expect to retail for around the $300 AUD mark.
The wording on the leaflet is
Suffering from headaches, back ache or joint problems?
At last....there is instant pain relief!
New to Australia, a personal portable pain relief device
Call Ned 0427581963 & 08 74925183
PLR Australia PO Box 612, Elmhurst SA 5093

Target Market(s)

aged, elderly

Industry/Entity Type

Retail

Font styles to use
Serif
Sans Serif

Colors
33b7a4
33a6d7
3176b5

Requirements
Must have
• include Free in house/office demonstration
Free $20 Norvan fuel card for first 11 demonstrations
Nice to have
• Norvane fuel logo

```html
<!DOCTYPE html>
<html lang="en">
<head>
<meta charset="utf-8">
<title>PLR Australia – Portable Pain Relief Flyer</title>
<link rel="stylesheet" href="https://fonts.googleapis.com/css2?family=Anton&family=Oswald:wght@600&display=swap">
<style>
  :root {
    --blue-deep: #253a8c;
    --blue-mid: #2f57b8;
    --blue-glow: #3a6fd0;
    --orange: #f47a20;
    --orange-light: #f7931e;
    --orange-dark: #c85a12;
    --ring: #ffffff;
    --ring-edge: #8fb6e8;
    --ink: #111111;
    --paper: #ffffff;
  }
  * { margin: 0; padding: 0; box-sizing: border-box; }
  html, body { width: 933px; height: 1200px; overflow: hidden; background: var(--blue-deep); }
  .flyer {
    position: relative; width: 933px; height: 1200px; overflow: hidden;
    background: radial-gradient(ellipse at 50% 45%, var(--blue-glow) 0%, var(--blue-mid) 40%, var(--blue-deep) 100%);
    font-family: "Oswald", "Arial Narrow", sans-serif;
  }
  .photo {
    position: absolute; border-radius: 50%;
    border: 7px solid var(--ring);
    box-shadow: 0 0 0 3px var(--ring-edge), 0 4px 10px rgba(0,0,0,.35);
  }
  .photo--pain { width: 148px; height: 148px; top: 37px; }
  .photo--happy { width: 160px; height: 160px; top: 379px; }
  .photo--head { left: 52px; background: linear-gradient(160deg, #e9dccb, #b9a58f); }
  .photo--knee { left: 274px; background: linear-gradient(160deg, #f1f1f1, #c89a7c); }
  .photo--back { left: 496px; background: linear-gradient(160deg, #f3f3f3, #b8785a); }
  .photo--couple { left: 290px; background: linear-gradient(160deg, #d9d0c6, #8a5a4a); }
  .photo--seniors { left: 505px; background: linear-gradient(160deg, #f2ede6, #9aa7b9); }
  .photo--woman { left: 720px; background: linear-gradient(160deg, #cfe0ee, #d8b48e); }

  .banner { position: absolute; }
  .banner svg { position: absolute; inset: 0; }
  .banner__text {
    position: relative; font-family: "Anton", "Impact", sans-serif;
    color: var(--ink); text-transform: uppercase; line-height: 1.14;
  }
  .banner--headline { left: 0; top: 181px; width: 880px; height: 152px; }
  .banner--headline .banner__text { font-size: 46px; padding: 14px 0 0 41px; letter-spacing: .5px; }
  .banner--offer { left: 230px; top: 533px; width: 703px; height: 134px; }
  .banner--offer .banner__text { font-size: 29px; text-align: center; padding: 16px 0 0 50px; line-height: 1.17; }

  .contact { position: absolute; left: 0; width: 933px; text-align: center; color: var(--paper); text-transform: uppercase; }
  .contact--phone { top: 700px; font-size: 35px; }
  .contact--address { top: 762px; font-size: 30px; line-height: 1.2; padding-right: 70px; }

  .arcs { position: absolute; left: 0; top: 0; }
  .badge { position: absolute; color: var(--paper); font-family: "Anton", "Impact", sans-serif; text-transform: uppercase; line-height: 1; }
  .badge--warranty { left: 40px; top: 900px; transform: rotate(-20deg); display: flex; align-items: center; }
  .badge--warranty .badge__num { font-size: 92px; }
  .badge--warranty .badge__label { font-size: 32px; margin-left: 4px; line-height: .95; }
  .badge--fuel { left: 690px; top: 858px; transform: rotate(24deg); text-align: center; }
  .badge--fuel .badge__big { font-size: 50px; }
  .badge--fuel .badge__small { font-size: 25px; }

  .offer-copy { position: absolute; left: 150px; width: 710px; top: 945px; text-align: center; color: var(--paper); text-transform: uppercase; font-size: 24px; line-height: 1.4; }
  .offer-copy p + p { margin-top: 22px; }
</style>
</head>
<body>
<div class="flyer">
  <div class="photo photo--pain photo--head" role="img" aria-label="Photo of a woman holding her head with a headache"></div>
  <div class="photo photo--pain photo--knee" role="img" aria-label="Photo of hands holding a painful knee joint"></div>
  <div class="photo photo--pain photo--back" role="img" aria-label="Photo of a bare back with the painful area highlighted in red"></div>

  <div class="banner banner--headline">
    <svg width="880" height="152" viewBox="0 0 880 152" aria-hidden="true">
      <defs><linearGradient id="orangeA" x1="0" x2="1"><stop offset="0" stop-color="#f47a20"/><stop offset="1" stop-color="#f7931e"/></linearGradient></defs>
      <polygon points="0,10 820,10 875,152 0,152" fill="var(--orange-dark)"/>
      <polygon points="0,0 810,0 862,142 0,142" fill="url(#orangeA)"/>
    </svg>
    <div class="banner__text">Suffering from headaches,<br>back ache or joint problems?</div>
  </div>

  <div class="photo photo--happy photo--couple" role="img" aria-label="Photo of a smiling older couple"></div>
  <div class="photo photo--happy photo--seniors" role="img" aria-label="Photo of a relaxed senior couple on a sofa"></div>
  <div class="photo photo--happy photo--woman" role="img" aria-label="Photo of a smiling young woman"></div>

  <div class="banner banner--offer">
    <svg width="703" height="134" viewBox="0 0 703 134" aria-hidden="true">
      <defs><linearGradient id="orangeB" x1="0" x2="1"><stop offset="0" stop-color="#f7931e"/><stop offset="1" stop-color="#f47a20"/></linearGradient></defs>
      <polygon points="0,8 703,8 703,134 48,134" fill="var(--orange-dark)"/>
      <polygon points="10,0 703,0 703,126 56,126" fill="url(#orangeB)"/>
    </svg>
    <div class="banner__text">At last….there is instant pain relief!<br>New to Australia, a personal portable<br>pain relief device</div>
  </div>

  <div class="contact contact--phone">Call Ned 0427581963 &amp; 08 74925183</div>
  <div class="contact contact--address">PLR Australia PO Box 612,<br>Elmhurst SA 5093</div>

  <svg class="arcs" width="933" height="1200" viewBox="0 0 933 1200" aria-hidden="true">
    <defs>
      <radialGradient id="dome" cx="0.5" cy="0.3" r="0.7"><stop offset="0" stop-color="#3a6fd0"/><stop offset="1" stop-color="#253a8c"/></radialGradient>
    </defs>
    <circle cx="120" cy="1340" r="495" fill="var(--orange)"/>
    <circle cx="120" cy="1340" r="485" fill="var(--paper)"/>
    <circle cx="120" cy="1340" r="478" fill="url(#dome)"/>
    <circle cx="840" cy="1265" r="505" fill="var(--orange)"/>
    <circle cx="840" cy="1265" r="495" fill="var(--paper)"/>
    <circle cx="840" cy="1265" r="488" fill="url(#dome)"/>
    <circle cx="480" cy="1330" r="440" fill="var(--orange)"/>
    <circle cx="480" cy="1330" r="428" fill="var(--paper)"/>
    <circle cx="480" cy="1330" r="421" fill="url(#dome)"/>
  </svg>

  <div class="badge badge--warranty">
    <span class="badge__num">3</span>
    <span class="badge__label">Year<br>Warranty</span>
  </div>
  <div class="badge badge--fuel">
    <div class="badge__big">Free $20</div>
    <div class="badge__small">Norvane fuel card</div>
  </div>

  <div class="offer-copy">
    <p>Try before you buy<br>at home/office demonstration,<br>a full 30 day money back guarantee<br>and a full 3 year warranty.</p>
    <p>We also plan to give the first 7 people<br>who book a demonstration a free $20 Norvane fuel card.</p>
  </div>
</div>
</body>
</html>
```